Looking for a modern, Professional business card design

We have a simple business card, but are looking for a more modern, professional look. A sample of the basic card is attached as well as the logo. We would also like to add that we offer:
Struggling with your finances?
- Learn to become debt free
- Discover the power of cash
- Control your money instead of it controlling you
Let us help you achieve a new level of financial freedom!
Also, we would like to have a "SPECIAL OFFER!: FREE 30 minute consultation"
Financial Planning

```html
<!DOCTYPE html>
<html lang="en">
<head>
<meta charset="UTF-8">
<title>Clearpath Money Coaching – Business Card</title>
<link rel="stylesheet" href="https://fonts.googleapis.com/css2?family=Source+Sans+3:ital,wght@0,400;0,600;0,700;1,400;1,700&display=swap">
<style>
  :root {
    --backdrop: #4d4d4d;
    --card-white: #ffffff;
    --card-black: #000000;
    --green-deep: #3f9444;
    --green-mid: #5fae3a;
    --green-light: #a6d23a;
    --green-head: #3aa64a;
    --lime: #8cc63f;
    --brand-green: #2f7d32;
    --text-white: #ffffff;
  }
  * { margin: 0; padding: 0; box-sizing: border-box; }
  html, body {
    width: 1105px;
    height: 1200px;
    overflow: hidden;
    background: var(--backdrop);
    font-family: "Source Sans 3", "Myriad Pro", Arial, sans-serif;
  }
  .card {
    position: absolute;
    left: 193px;
    width: 718px;
    height: 412px;
    overflow: hidden;
  }
  .card--front { top: 181px; background: var(--card-white); }
  .card--back  { top: 623px; background: var(--card-black); }

  .front-swoosh { position: absolute; inset: 0; width: 100%; height: 100%; }

  .brand {
    position: absolute;
    display: flex;
    align-items: center;
    gap: 12px;
    font-weight: 700;
    color: var(--brand-green);
    letter-spacing: 0.5px;
  }
  .brand__dot {
    border-radius: 50%;
    background: var(--brand-green);
    flex: none;
  }
  .card--front .brand { left: 32px; top: 52px; font-size: 30px; }
  .card--front .brand__dot { width: 34px; height: 34px; }

  .contact {
    position: absolute;
    right: 40px;
    top: 182px;
    text-align: right;
    color: var(--text-white);
  }
  .contact__name { font-size: 26px; font-weight: 600; letter-spacing: 0.5px; line-height: 1.1; }
  .contact__title { font-size: 19px; font-weight: 400; margin-top: 4px; letter-spacing: 0.3px; }
  .contact__lines { margin-top: 30px; font-size: 19px; line-height: 1.4; }
  .contact__label { font-weight: 700; }

  .card--back .brand {
    left: 0; right: 0; top: 80px;
    justify-content: center;
    font-size: 32px;
    color: var(--lime);
  }
  .card--back .brand__dot { width: 34px; height: 34px; background: var(--lime); }

  .pitch {
    position: absolute;
    left: 0; right: 0; top: 240px;
    text-align: center;
    color: var(--text-white);
  }
  .pitch__headline {
    font-size: 21px;
    font-weight: 600;
    color: var(--green-head);
    letter-spacing: 0.4px;
    margin-bottom: 2px;
  }
  .pitch__lines { font-size: 18.5px; font-style: italic; line-height: 1.4; }
  .pitch__bullet { color: var(--green-head); font-style: normal; margin: 0 6px; }
  .pitch__offer {
    margin-top: 12px;
    font-size: 27px;
    font-weight: 700;
    font-style: italic;
    color: var(--lime);
  }
</style>
</head>
<body>
  <section class="card card--front">
    <svg class="front-swoosh" viewBox="0 0 718 412" preserveAspectRatio="none" aria-hidden="true">
      <defs>
        <radialGradient id="swoosh-fill" cx="0.6" cy="0.42" r="0.6">
          <stop offset="0" stop-color="var(--green-light)"/>
          <stop offset="0.55" stop-color="var(--green-mid)"/>
          <stop offset="1" stop-color="var(--green-deep)"/>
        </radialGradient>
      </defs>
      <path d="M0,412 L0,232 C220,254 400,196 718,0 L718,412 Z" fill="var(--green-deep)"/>
      <path d="M0,412 L0,246 C230,268 410,210 718,14 L718,412 Z" fill="url(#swoosh-fill)"/>
    </svg>

    <div class="brand">
      <span class="brand__dot"></span>
      <span class="brand__name">Clearpath Money Coaching</span>
    </div>

    <div class="contact">
      <p class="contact__name">DANIEL R. HAYES</p>
      <p class="contact__title">PERSONAL FINANCIAL COACH</p>
      <div class="contact__lines">
        <p><span class="contact__label">Mobile:</span> (205) 555-0147</p>
        <p>daniel@clearpathcoaching.com</p>
        <p>www.clearpathcoaching.com</p>
      </div>
    </div>
  </section>

  <section class="card card--back">
    <div class="brand">
      <span class="brand__dot"></span>
      <span class="brand__name">Clearpath Money Coaching</span>
    </div>

    <div class="pitch">
      <p class="pitch__headline">STRUGGLING WITH YOUR FINANCES?</p>
      <div class="pitch__lines">
        <p>Learn to become debt free<span class="pitch__bullet">•</span>Discover the power of cash</p>
        <p>Control your money instead of it controlling you</p>
        <p>Let us help you achieve a new level of financial freedom!</p>
      </div>
      <p class="pitch__offer">SPECIAL OFFER!: FREE 30 minute consultation</p>
    </div>
  </section>
</body>
</html>
```